Oil and Gas Exploration and Production company needs a business card design

We need a business card design using our logo and colors in the logo. We want a mainstream design.

```html
<!DOCTYPE html>
<html lang="en">
<head>
<meta charset="utf-8">
<title>Quillmere Oil &amp; Gas – Business Card</title>
<link rel="stylesheet" href="https://fonts.googleapis.com/css2?family=Lato:wght@400;700;900&display=swap">
<style>
  :root {
    --backdrop: #2b2b2b;
    --card-white: #f4f4f4;
    --card-black: #0b0b0b;
    --gold: #b8862b;
    --ink: #111111;
    --light-text: #e6e6e6;
  }
  html, body {
    margin: 0;
    padding: 0;
    width: 1200px;
    height: 997px;
    overflow: hidden;
    background: var(--backdrop);
    font-family: "Lato", Arial, sans-serif;
  }
  .business-card {
    position: absolute;
    left: 180px;
    top: 258px;
    width: 840px;
    height: 480px;
    background: var(--card-white);
    overflow: hidden;
    box-shadow: 0 20px 40px rgba(0,0,0,0.5);
  }
  .card-shapes {
    position: absolute;
    inset: 0;
  }
  .brand {
    position: absolute;
    left: 0;
    right: 0;
    top: 88px;
    display: flex;
    justify-content: center;
    align-items: center;
    gap: 16px;
  }
  .brand-dot {
    width: 40px;
    height: 40px;
    border-radius: 50%;
    background: var(--gold);
  }
  .brand-name {
    font-weight: 900;
    font-size: 54px;
    line-height: 1;
    color: var(--ink);
    white-space: nowrap;
  }
  .contact-person {
    position: absolute;
    left: 120px;
    top: 358px;
    width: 272px;
    text-align: right;
  }
  .person-name {
    font-weight: 700;
    font-size: 21px;
    color: var(--gold);
    text-transform: uppercase;
    letter-spacing: 0.5px;
  }
  .person-role {
    font-size: 17px;
    color: var(--light-text);
    margin-top: 4px;
  }
  .divider {
    position: absolute;
    left: 420px;
    top: 300px;
    width: 2px;
    height: 140px;
    background: linear-gradient(to bottom, transparent, var(--gold), transparent);
  }
  .contact-list {
    position: absolute;
    left: 445px;
    top: 300px;
    list-style: none;
    margin: 0;
    padding: 0;
  }
  .contact-item {
    display: flex;
    align-items: center;
    gap: 14px;
    height: 40px;
    font-size: 17px;
    color: var(--light-text);
    white-space: nowrap;
  }
  .contact-item.website {
    color: var(--gold);
    font-weight: 700;
  }
  .contact-icon {
    width: 22px;
    height: 22px;
    border-radius: 50%;
    background: var(--gold);
    display: flex;
    align-items: center;
    justify-content: center;
    flex: none;
  }
  .contact-icon svg {
    width: 12px;
    height: 12px;
  }
</style>
</head>
<body>
  <section class="business-card">
    <svg class="card-shapes" viewBox="0 0 840 480" width="840" height="480" aria-hidden="true">
      <path class="black-panel" d="M0 372 C 200 268, 520 208, 840 212 L840 480 L0 480 Z" fill="var(--card-black)"/>
      <path class="gold-swoosh" d="M105 338 C 300 232, 560 182, 792 184 C 560 194, 300 246, 105 338 Z" fill="var(--gold)"/>
    </svg>

    <div class="brand">
      <span class="brand-dot"></span>
      <span class="brand-name">Quillmere Oil &amp; Gas</span>
    </div>

    <div class="contact-person">
      <div class="person-name">Daniel Hartley</div>
      <div class="person-role">General Manager</div>
    </div>

    <div class="divider"></div>

    <ul class="contact-list">
      <li class="contact-item">
        <span class="contact-icon">
          <svg viewBox="0 0 12 12"><path d="M2 1.5 L4 1 L5 3.5 L3.8 4.5 C4.4 6 5.8 7.5 7.5 8.2 L8.5 7 L11 8 L10.5 10 C6 10.5 1.5 6 2 1.5 Z" fill="#111"/></svg>
        </span>
        0161 496 0142
      </li>
      <li class="contact-item">
        <span class="contact-icon">
          <svg viewBox="0 0 12 12"><rect x="3.5" y="1" width="5" height="10" rx="1" fill="none" stroke="#111" stroke-width="1.2"/><circle cx="6" cy="9.3" r="0.6" fill="#111"/></svg>
        </span>
        dhartley@quillmere-energy.co.uk
      </li>
      <li class="contact-item website">
        <span class="contact-icon">
          <svg viewBox="0 0 12 12"><rect x="1.5" y="3" width="9" height="6.5" fill="none" stroke="#111" stroke-width="1.2"/><path d="M1.5 3 L6 7 L10.5 3" fill="none" stroke="#111" stroke-width="1.2"/></svg>
        </span>
        www.quillmere-energy.co.uk
      </li>
    </ul>
  </section>
</body>
</html>
```